Need Business Card ASAP

We need a business card design for a meeting coming up in a few days. The company name is Harlow Ridge Building and Construction and the logo is attached. Something clean, cool, and contemporary that we can get to a printer right away. Attached is the business card for Volmar Energy, an affiliated company, which we like. Instead of the hawk on the back, you could use the attached "D". We'll also be needing matching letterhead in the near future, so ideas for that are welcome.

```html
<!DOCTYPE html>
<html lang="en">
<head>
<meta charset="utf-8">
<title>Harlow Ridge Building and Construction – Business Card</title>
<link href="https://fonts.googleapis.com/css2?family=Source+Sans+3:wght@400;600;700&display=swap" rel="stylesheet">
<style>
  :root {
    --backdrop: #8a6a4a;
    --card-white: #ffffff;
    --band-grey: #dcdcdc;
    --rule-grey: #d4d4d4;
    --gold: #bcb27c;
    --gold-light: #dcd8bc;
    --gold-mid: #cbc49e;
    --ink: #2a2a2a;
    --text: #333333;
  }
  * { margin: 0; padding: 0; box-sizing: border-box; }
  html, body { width: 1034px; height: 1200px; overflow: hidden; }
  body {
    background: var(--backdrop);
    font-family: "Source Sans 3", Arial, sans-serif;
    position: relative;
  }
  .card {
    position: absolute;
    width: 889px;
    height: 507px;
    overflow: hidden;
    box-shadow: 0 3px 10px rgba(0,0,0,0.35);
  }
  /* Front */
  .card-front { left: 74px; top: 68px; background: var(--card-white); }
  .band { position: absolute; left: 0; width: 100%; height: 71px; background: var(--band-grey); }
  .band-top { top: 0; }
  .band-bottom { bottom: 0; }
  .company-name {
    position: absolute; left: 308px; top: 78px;
    font-size: 31px; font-weight: 600; color: var(--gold); letter-spacing: 0.2px;
  }
  .company-address {
    position: absolute; left: 308px; top: 118px;
    font-size: 23px; color: var(--text);
  }
  .rule { position: absolute; top: 164px; height: 7px; }
  .rule-grey { left: 0; width: 610px; background: var(--rule-grey); }
  .rule-gold { left: 622px; width: 267px; background: var(--gold); }
  .brand-block {
    position: absolute; left: 37px; top: 191px; width: 171px; height: 218px;
    display: flex; flex-direction: column; align-items: center; justify-content: center; gap: 18px;
  }
  .brand-square { width: 70px; height: 70px; background: var(--gold); }
  .brand-name {
    font-size: 22px; font-weight: 600; color: var(--ink);
    text-align: center; line-height: 1.15;
  }
  .person { position: absolute; left: 308px; top: 190px; }
  .person-name { font-size: 31px; font-weight: 700; color: var(--gold); line-height: 1.1; }
  .person-title { font-size: 22px; font-weight: 600; color: var(--text); margin-top: 2px; }
  .contact-list { position: absolute; left: 308px; top: 275px; list-style: none; }
  .contact-list li {
    display: flex; align-items: center; gap: 8px;
    font-size: 23px; color: var(--text); height: 39px;
  }
  .contact-list svg { width: 18px; height: 18px; flex: none; }
  /* Back */
  .card-back {
    left: 71px; top: 615px;
    background: linear-gradient(180deg, var(--gold-mid) 0%, var(--gold-light) 100%);
    display: flex; align-items: center; justify-content: center;
  }
  .back-name {
    font-size: 50px; font-weight: 600; color: var(--card-white);
    text-align: center; line-height: 1.15;
  }
</style>
</head>
<body>
  <section class="card card-front">
    <div class="band band-top"></div>
    <div class="company-name">Harlow Ridge Building and Construction</div>
    <div class="company-address">00, Complex Name, Street, City 00000</div>
    <div class="rule rule-grey"></div>
    <div class="rule rule-gold"></div>

    <div class="brand-block">
      <div class="brand-square"></div>
      <div class="brand-name">Harlow Ridge</div>
    </div>

    <div class="person">
      <div class="person-name">Your Name</div>
      <div class="person-title">Title</div>
    </div>

    <ul class="contact-list">
      <li>
        <svg viewBox="0 0 20 20"><circle cx="10" cy="10" r="8.5" fill="none" stroke="#999" stroke-width="1.5"/><path d="M7 6c0 4 3 7 7 7l-1.5-2-1.5.5-2.5-2.5.5-1.5z" fill="#999"/></svg>
        (123) 456-7890
      </li>
      <li>
        <svg viewBox="0 0 20 20"><rect x="6" y="2" width="8" height="16" rx="1.5" fill="none" stroke="#999" stroke-width="1.5"/><rect x="7.5" y="4.5" width="5" height="7" fill="#999"/></svg>
        (123) 456-7890
      </li>
      <li>
        <svg viewBox="0 0 20 20"><rect x="2" y="5" width="16" height="11" fill="#999"/><path d="M2 5l8 6 8-6" fill="none" stroke="#fff" stroke-width="1.3"/></svg>
        yourname@harlowridgebuild.com
      </li>
      <li>
        <svg viewBox="0 0 20 20"><circle cx="10" cy="10" r="8" fill="none" stroke="#999" stroke-width="1.5"/><ellipse cx="10" cy="10" rx="3.5" ry="8" fill="none" stroke="#999" stroke-width="1.3"/><path d="M2 10h16" stroke="#999" stroke-width="1.3"/></svg>
        www.harlowridgebuild.com
      </li>
    </ul>
    <div class="band band-bottom"></div>
  </section>

  <section class="card card-back">
    <div class="back-name">Harlow Ridge<br>Building and Construction</div>
  </section>
</body>
</html>
```